Web Developer Needs a Business Card Design

I need a personal business card design that represents me as a web developer for potential employers. I would like the background to be a dark color on the front for contrast with my logo and name. The back will have all my information along with a smaller version of the logo. I want something with a modern look and feel, not too conservative. This will be used for potential employers and freelance work.

Industry/Entity Type

Business

Contact Information for Business Card

Front should have my logo and name. The back should have all my personal information which would include: name: Tom Varulek, phone: 570-614-3098, email: tomvarulek@quillbox.net, website url: www.tomvarulek.net, logo, web developer.

Font styles to use
Sans Serif

Requirements
Must have
• Must include my logo. The color palette base color will be the logo color.

```html
<!DOCTYPE html>
<html lang="en">
<head>
<meta charset="utf-8">
<title>Tom Varulek — Business Cards</title>
<link href="https://fonts.googleapis.com/css2?family=Open+Sans:wght@400;600;700&display=swap" rel="stylesheet">
<style>
  :root {
    --teal: #5cc6aa;
    --ink: #1c1c1c;
    --ink-mid: #2f2f2f;
    --ink-light: #444444;
    --paper: #ffffff;
    --text-grey: #4a4a4a;
    --stage: #e9e7e3;
  }
  * { box-sizing: border-box; margin: 0; padding: 0; }
  html, body {
    width: 1200px; height: 913px; overflow: hidden;
    background: var(--stage);
    font-family: "Open Sans", Arial, sans-serif;
  }
  .canvas { position: relative; width: 1200px; height: 913px; }

  .card {
    position: absolute;
    width: 520px; height: 300px;
    border-radius: 18px;
    overflow: hidden;
    box-shadow: 0 14px 30px rgba(0,0,0,0.22);
  }

  /* Contact side */
  .card--contact { left: 90px; top: 110px; background: var(--paper); }
  .card--contact .curve { position: absolute; inset: 0; }
  .contact-brand {
    position: absolute; left: 44px; top: 218px;
    display: flex; align-items: center; gap: 12px;
  }
  .brand-dot {
    width: 26px; height: 26px; border-radius: 50%;
    background: var(--teal);
  }
  .brand-name {
    font-size: 32px; font-weight: 600; color: var(--teal);
    letter-spacing: 0.5px;
  }
  .contact-details {
    position: absolute; right: 34px; top: 34px;
    text-align: right;
  }
  .contact-name {
    font-size: 22px; font-weight: 700; color: var(--text-grey);
    letter-spacing: 1px; text-transform: uppercase; line-height: 1.1;
  }
  .contact-role {
    font-size: 13px; font-weight: 600; color: var(--teal);
    letter-spacing: 1px; text-transform: uppercase; margin-bottom: 12px;
  }
  .contact-line {
    display: flex; justify-content: flex-end; align-items: center; gap: 8px;
    font-size: 14px; color: var(--text-grey); line-height: 22px;
  }
  .contact-line svg { width: 13px; height: 13px; flex: none; }

  /* Front side */
  .card--front {
    left: 590px; top: 500px;
    background: linear-gradient(135deg, var(--ink-light) 0%, var(--ink-mid) 45%, var(--ink) 100%);
    display: flex; flex-direction: column; align-items: center; justify-content: center;
  }
  .front-brand {
    display: flex; align-items: center; gap: 10px; margin-bottom: 22px;
  }
  .front-brand .brand-dot { width: 20px; height: 20px; }
  .front-brand .brand-name { font-size: 26px; }
  .front-name {
    font-size: 30px; font-weight: 400; color: var(--paper);
    letter-spacing: 3px; text-transform: uppercase;
  }
  .front-role {
    font-size: 16px; color: #e6e6e6; letter-spacing: 1px; margin-top: 6px;
  }
</style>
</head>
<body>
<main class="canvas">

  <section class="card card--contact" aria-label="Contact side">
    <svg class="curve" viewBox="0 0 520 300" width="520" height="300" aria-hidden="true">
      <defs>
        <linearGradient id="darkPanel" x1="0" y1="0" x2="1" y2="1">
          <stop offset="0" stop-color="#4a4a4a"/>
          <stop offset="0.5" stop-color="#2b2b2b"/>
          <stop offset="1" stop-color="#1a1a1a"/>
        </linearGradient>
      </defs>
      <path d="M0 168 Q372 108 452 300 L0 300 Z" fill="var(--teal)"/>
      <path d="M0 174 Q366 114 446 300 L0 300 Z" fill="var(--paper)"/>
      <path d="M0 180 Q360 120 440 300 L0 300 Z" fill="url(#darkPanel)"/>
    </svg>

    <div class="contact-brand">
      <span class="brand-dot"></span>
      <span class="brand-name">Varulek</span>
    </div>

    <div class="contact-details">
      <p class="contact-name">Tom Varulek</p>
      <p class="contact-role">Web Developer</p>
      <p class="contact-line">570-614-3098
        <svg viewBox="0 0 24 24" fill="var(--teal)" aria-hidden="true"><path d="M6.6 10.8a15 15 0 0 0 6.6 6.6l2.2-2.2c.3-.3.7-.4 1-.2 1.1.4 2.3.6 3.6.6.6 0 1 .4 1 1V20c0 .6-.4 1-1 1C10.6 21 3 13.4 3 4c0-.6.4-1 1-1h3.5c.6 0 1 .4 1 1 0 1.2.2 2.4.6 3.6.1.3 0 .7-.2 1z"/></svg>
      </p>
      <p class="contact-line">tomvarulek@quillbox.net
        <svg viewBox="0 0 24 24" fill="none" stroke="var(--teal)" stroke-width="2" aria-hidden="true"><rect x="3" y="5" width="18" height="14" rx="1"/><path d="M3 6l9 7 9-7"/></svg>
      </p>
      <p class="contact-line">www.tomvarulek.net
        <svg viewBox="0 0 24 24" fill="none" stroke="var(--teal)" stroke-width="2" aria-hidden="true"><circle cx="12" cy="12" r="9"/><path d="M3 12h18M12 3c3 3 3 15 0 18M12 3c-3 3-3 15 0 18"/></svg>
      </p>
    </div>
  </section>

  <section class="card card--front" aria-label="Front side">
    <div class="front-brand">
      <span class="brand-dot"></span>
      <span class="brand-name">Varulek</span>
    </div>
    <p class="front-name">Tom Varulek</p>
    <p class="front-role">Front-End Developer</p>
  </section>

</main>
</body>
</html>
```